Business cards and stationary design

We just completed the design of our new logo and we need to print new business cards and letterhead for our nonprofit. We are looking for a fresh new design that shows off our new logo. On letterhead, we must have a column on the right or left to include our Board of Directors (up to 45 names) (see attachment)

Industry/Entity Type

Non-Profit

Contact Information for Business Card

Standard business card with name, title, Company name, mailing address phone numbers, email address and website. Tagline on back "Bringing the homeless home"

Font styles to use
Sans Serif

Requirements
Must have
• include pertinent information above
• new logo
• fonts compatible with logo
• should use logo colors only
Nice to have
• tag lines

```html
<!DOCTYPE html>
<html lang="en">
<head>
<meta charset="utf-8">
<title>Hearthway Shelter Network – Business Card</title>
<link rel="stylesheet" href="https://fonts.googleapis.com/css2?family=Exo+2:wght@500;600;700&display=swap">
<style>
  :root {
    --red: #e30613;
    --teal: #00728f;
    --gold: #f2a900;
    --ink: #333a40;
    --paper: #ffffff;
    --backdrop: #e9e6e1;
  }
  * { box-sizing: border-box; margin: 0; padding: 0; }
  html, body {
    width: 1200px; height: 800px; overflow: hidden;
    background: var(--backdrop);
    font-family: "Exo 2", sans-serif;
  }
  .canvas { position: relative; width: 1200px; height: 800px; }
  .card {
    position: absolute; top: 250px;
    width: 525px; height: 300px;
    background: var(--paper);
    box-shadow: 0 6px 18px rgba(0,0,0,.15);
    overflow: hidden;
  }
  .card--back { left: 55px; }
  .card--front { left: 620px; }

  /* back */
  .back-geometry { position: absolute; inset: 0; }
  .back-website {
    position: absolute; top: 26px; right: 26px;
    color: var(--teal); font-weight: 600; font-size: 14px; letter-spacing: 1.5px;
  }
  .back-brand {
    position: absolute; right: 30px; top: 150px; text-align: right;
  }
  .back-brand__name {
    display: flex; align-items: center; gap: 10px; justify-content: flex-end;
    color: var(--teal); font-weight: 700; font-size: 24px; letter-spacing: 2px;
  }
  .brand-dot { width: 14px; height: 14px; border-radius: 50%; background: var(--gold); }
  .back-brand__rule { margin-top: 10px; height: 2px; background: var(--red); }

  /* front */
  .front-name {
    position: absolute; top: 34px; left: 30px;
    border-left: 4px solid var(--gold); padding-left: 10px;
  }
  .front-name__person { color: var(--red); font-weight: 700; font-size: 22px; letter-spacing: 1.5px; line-height: 1.1; }
  .front-name__title { color: var(--ink); font-weight: 600; font-size: 14px; letter-spacing: 1.5px; }
  .front-brand {
    position: absolute; top: 118px; right: 34px;
    display: flex; align-items: center; gap: 10px;
    color: var(--teal); font-weight: 700; font-size: 22px; letter-spacing: 2px;
  }
  .front-contact { position: absolute; left: 30px; bottom: 52px; list-style: none; }
  .front-contact li {
    display: flex; align-items: center; gap: 10px;
    color: var(--ink); font-weight: 600; font-size: 15px; letter-spacing: 1px;
    margin-top: 8px;
  }
  .contact-icon { width: 22px; height: 22px; flex: none; }
  .front-address {
    position: absolute; right: 30px; bottom: 26px; text-align: right;
    color: var(--teal); font-weight: 600; font-size: 14px; letter-spacing: 1.5px; line-height: 1.3;
  }
</style>
</head>
<body>
<main class="canvas">

  <section class="card card--back" aria-label="Business card, back">
    <svg class="back-geometry" viewBox="0 0 525 300" width="525" height="300" aria-hidden="true">
      <polygon points="0,0 232,0 215,190 0,95" fill="var(--red)"/>
      <polygon points="0,95 215,190 345,300 0,300" fill="var(--teal)"/>
    </svg>
    <p class="back-website">WWW.HEARTHWAYDALLAS.ORG</p>
    <div class="back-brand">
      <p class="back-brand__name"><span class="brand-dot"></span>HEARTHWAY</p>
      <div class="back-brand__rule"></div>
    </div>
  </section>

  <section class="card card--front" aria-label="Business card, front">
    <div class="front-name">
      <p class="front-name__person">JOHN DOE</p>
      <p class="front-name__title">DIRECTOR</p>
    </div>

    <p class="front-brand"><span class="brand-dot"></span>HEARTHWAY</p>

    <ul class="front-contact">
      <li>
        <svg class="contact-icon" viewBox="0 0 22 22" aria-hidden="true">
          <circle cx="11" cy="11" r="11" fill="var(--red)"/>
          <path d="M7.5 6.5c.6-.6 1.4-.5 1.8.1l.9 1.5c.3.5.2 1-.2 1.4l-.5.5c.6 1.2 1.5 2.1 2.6 2.7l.5-.5c.4-.4 1-.5 1.4-.2l1.5.9c.6.4.7 1.2.1 1.8l-.6.6c-.8.8-2.2.7-3.9-.3-1.4-.8-2.7-2.1-3.5-3.5-1-1.7-1.1-3.1-.3-3.9z" fill="#fff"/>
        </svg>
        214.555.0187
      </li>
      <li>
        <svg class="contact-icon" viewBox="0 0 22 22" aria-hidden="true">
          <circle cx="11" cy="11" r="11" fill="var(--red)"/>
          <rect x="5.5" y="7.5" width="11" height="7.5" rx="1" fill="#fff"/>
          <path d="M5.8 8l5.2 4 5.2-4" fill="none" stroke="var(--red)" stroke-width="1.2"/>
        </svg>
        EMAIL@hearthwaydallas.org
      </li>
    </ul>

    <p class="front-address">P.O. BOX 2290<br>DALLAS, TEXAS 75214</p>
  </section>

</main>
</body>
</html>
```